New Business Card Design Project

Need a design that will create an impact / strong impression towards our clients for our business. We are in the lighting business and we do lighting retrofits for large commercial to industrial clientele.

Target Market(s)

Lighting Industry

Industry/Entity Type

Business

Font styles to use
Other font styles liked:
• we would like to use the font on our logo, not sure what it is though..

Requirements
Must have
• Our logo.
Nice to have
• We are open to suggestions that have to do with lighting.

```html
<!DOCTYPE html>
<html lang="en">
<head>
<meta charset="utf-8">
<title>Lumenward Retrofit Group – Business Card</title>
<link rel="stylesheet" href="https://fonts.googleapis.com/css2?family=Lato:wght@400;700;900&display=swap">
<style>
  :root {
    --backdrop: #3b3b3b;
    --paper: #ffffff;
    --forest: #0f3f10;
    --leaf: #1f8a3a;
    --lime: #5cc45a;
    --ink: #1d1d1d;
  }
  * { margin: 0; padding: 0; box-sizing: border-box; }
  html, body { width: 1200px; height: 900px; overflow: hidden; }
  body {
    background: var(--backdrop);
    font-family: "Lato", Arial, sans-serif;
    display: flex;
    flex-direction: column;
    align-items: center;
    justify-content: center;
    gap: 40px;
  }
  .card {
    position: relative;
    width: 700px;
    height: 400px;
    background: var(--paper);
    overflow: hidden;
  }
  .brand {
    display: flex;
    align-items: center;
    gap: 14px;
    color: var(--forest);
    font-weight: 900;
  }
  .brand-mark {
    width: 22px;
    height: 22px;
    background: var(--leaf);
    flex: none;
  }
  .brand-name { line-height: 1; }
  .brand-name .primary { display: block; font-size: 64px; letter-spacing: 1px; }
  .brand-name .secondary { display: block; font-size: 17px; letter-spacing: 3px; margin-top: 8px; }

  /* front */
  .card-front .brand { position: absolute; left: 50%; top: 110px; transform: translateX(-50%); }
  .card-front .website {
    position: absolute;
    left: 0; right: 0; bottom: 70px;
    text-align: center;
    font-size: 17px;
    letter-spacing: 1px;
    color: var(--ink);
  }

  /* back */
  .card-back .brand { position: absolute; left: 40px; top: 45px; }
  .card-back .brand-name .primary { font-size: 52px; }
  .card-back .brand-name .secondary { font-size: 14px; }
  .wave { position: absolute; inset: 0; width: 700px; height: 400px; }
  .address {
    position: absolute;
    left: 40px; top: 280px;
    color: var(--paper);
    font-size: 23px;
    line-height: 1.3;
  }
  .contact {
    position: absolute;
    right: 28px; top: 222px;
    text-align: right;
    color: var(--paper);
  }
  .contact-name { font-size: 29px; font-weight: 700; line-height: 1.1; padding-right: 34px; }
  .contact-role { font-size: 19px; color: var(--leaf); margin-bottom: 10px; padding-right: 34px; }
  .contact-list { list-style: none; font-size: 19px; line-height: 1.45; }
  .contact-list li { display: flex; justify-content: flex-end; align-items: center; gap: 12px; }
  .contact-list svg { width: 20px; height: 20px; fill: var(--leaf); flex: none; }
</style>
</head>
<body>

<section class="card card-front">
  <div class="brand">
    <span class="brand-mark"></span>
    <span class="brand-name"><span class="primary">LUMENWARD</span><span class="secondary">RETROFIT GROUP, LLC</span></span>
  </div>
  <p class="website">www.lumenward-retrofit.com</p>
</section>

<section class="card card-back">
  <svg class="wave" viewBox="0 0 700 400" aria-hidden="true">
    <path fill="var(--forest)" d="M0,222 C180,258 380,258 500,200 C590,155 640,80 700,10 L700,400 L0,400 Z"/>
    <path fill="var(--leaf)" d="M330,250 C470,240 580,170 648,0 L672,0 C600,175 480,248 330,250 Z"/>
  </svg>

  <div class="brand">
    <span class="brand-mark"></span>
    <span class="brand-name"><span class="primary">LUMENWARD</span><span class="secondary">RETROFIT GROUP, LLC</span></span>
  </div>

  <p class="address">2148 Alder Park Road<br>Oakmont, IL 60900</p>

  <div class="contact">
    <p class="contact-name">Marcus Hale</p>
    <p class="contact-role">Manager</p>
    <ul class="contact-list">
      <li>(555) 014-2200
        <svg viewBox="0 0 24 24"><path d="M6.6 10.8a15.5 15.5 0 0 0 6.6 6.6l2.2-2.2a1 1 0 0 1 1-.25 11.4 11.4 0 0 0 3.6.57 1 1 0 0 1 1 1V20a1 1 0 0 1-1 1A17 17 0 0 1 3 4a1 1 0 0 1 1-1h3.5a1 1 0 0 1 1 1c0 1.25.2 2.45.57 3.57a1 1 0 0 1-.25 1z"/></svg></li>
      <li>(555) 014-2201
        <svg viewBox="0 0 24 24"><path d="M7 3h10v4H7zM4 8h16a2 2 0 0 1 2 2v6h-4v5H6v-5H2v-6a2 2 0 0 1 2-2zm4 8v3h8v-3z"/></svg></li>
      <li>info@lumenward-retrofit.com
        <svg viewBox="0 0 24 24"><path d="M2 5h20v14H2zm2 2v.5l8 5 8-5V7zm0 3v7h16v-7l-8 5z"/></svg></li>
      <li>www.lumenward-retrofit.com
        <svg viewBox="0 0 24 24"><path d="M12 2a10 10 0 1 0 0 20 10 10 0 0 0 0-20zm6.9 6h-3a15 15 0 0 0-1.3-3.9A8 8 0 0 1 18.9 8zM12 4c.8 1.1 1.5 2.5 1.9 4h-3.8c.4-1.5 1.1-2.9 1.9-4zM4.3 14a8 8 0 0 1 0-4h3.4a16 16 0 0 0 0 4zm.8 2h3a15 15 0 0 0 1.3 3.9A8 8 0 0 1 5.1 16zm3-8h-3a8 8 0 0 1 4.3-3.9A15 15 0 0 0 8.1 8zM12 20c-.8-1.1-1.5-2.5-1.9-4h3.8c-.4 1.5-1.1 2.9-1.9 4zm2.3-6H9.7a14 14 0 0 1 0-4h4.6a14 14 0 0 1 0 4zm.3 5.9a15 15 0 0 0 1.3-3.9h3a8 8 0 0 1-4.3 3.9zm1.7-5.9a16 16 0 0 0 0-4h3.4a8 8 0 0 1 0 4z"/></svg></li>
    </ul>
  </div>
</section>

</body>
</html>
```